Business card design for Brivo Engineering Tandem

We need a new business card design along with all the necessary to place an order. The company is Brivo Engineering Tandem and we recently updated our logo.

```html
<!DOCTYPE html>
<html lang="en">
<head>
<meta charset="utf-8">
<title>Brivo Engineering Tandem – Business Card</title>
<link rel="stylesheet" href="https://fonts.googleapis.com/css2?family=Poppins:wght@400;500;600&display=swap">
<style>
  :root {
    --backdrop: #6b6b6b;
    --card-white: #ffffff;
    --brand-yellow: #e2bd22;
    --brand-grey: #939393;
    --ink: #111111;
  }
  * { margin: 0; padding: 0; box-sizing: border-box; }
  html, body {
    width: 1093px; height: 1200px; overflow: hidden;
    background: var(--backdrop);
    font-family: "Poppins", sans-serif;
  }
  .canvas { position: relative; width: 1093px; height: 1200px; }
  .card {
    position: absolute; left: 264px; width: 580px; height: 357px;
    overflow: hidden;
  }
  .card--front { top: 226px; background: var(--brand-yellow); color: var(--ink); }
  .card--back { top: 620px; background: var(--card-white); }

  .holder { position: absolute; left: 26px; top: 40px; }
  .holder__name { font-weight: 600; font-size: 22px; line-height: 1.05; letter-spacing: 0.2px; }
  .holder__role { font-weight: 400; font-size: 16px; line-height: 1.2; }
  .rule { position: absolute; left: 26px; width: 31px; height: 1.5px; background: var(--ink); }
  .rule--one { top: 96px; }
  .rule--two { top: 191px; }

  .contacts { position: absolute; left: 26px; top: 113px; list-style: none; }
  .contacts li { display: flex; align-items: center; font-size: 16px; line-height: 21px; }
  .contacts svg { width: 15px; height: 15px; margin-right: 7px; flex: none; }

  .address { position: absolute; left: 27px; top: 207px; font-size: 16px; line-height: 21px; font-style: normal; }

  .wordmark {
    position: absolute; left: 0; right: 0; top: 160px;
    display: flex; justify-content: center; align-items: center; gap: 12px;
  }
  .wordmark__square { width: 16px; height: 16px; background: var(--brand-yellow); }
  .wordmark__name {
    font-weight: 500; font-size: 27px; color: var(--brand-grey);
    text-transform: uppercase; letter-spacing: 1.5px;
  }

  .web {
    position: absolute; left: 0; right: 0; top: 292px;
    display: flex; justify-content: center; align-items: center; gap: 8px;
    font-size: 16px; letter-spacing: 2.4px; color: var(--brand-grey);
  }
  .web__line { width: 47px; height: 1.5px; background: var(--brand-yellow); }
  .web__accent { color: var(--brand-yellow); }
</style>
</head>
<body>
<main class="canvas">
  <section class="card card--front">
    <div class="holder">
      <h1 class="holder__name">DANIEL MERCER</h1>
      <p class="holder__role">Managing Director</p>
    </div>
    <span class="rule rule--one"></span>
    <ul class="contacts">
      <li>
        <svg viewBox="0 0 24 24" aria-hidden="true"><path fill="currentColor" d="M6.6 10.8a15.1 15.1 0 0 0 6.6 6.6l2.2-2.2a1 1 0 0 1 1-.25 11.4 11.4 0 0 0 3.6.57 1 1 0 0 1 1 1V20a1 1 0 0 1-1 1A17 17 0 0 1 3 4a1 1 0 0 1 1-1h3.5a1 1 0 0 1 1 1c0 1.25.2 2.45.57 3.57a1 1 0 0 1-.25 1z"/></svg>
        044-555 010 234
      </li>
      <li>
        <svg viewBox="0 0 24 24" aria-hidden="true"><path fill="currentColor" d="M2 5h20v14H2z M2 5l10 8 10-8" stroke="#e2bd22" stroke-width="1.5"/></svg>
        hello@brivotandem.com
      </li>
      <li>
        <svg viewBox="0 0 24 24" aria-hidden="true"><g fill="none" stroke="currentColor" stroke-width="1.8"><circle cx="12" cy="12" r="9.5"/><ellipse cx="12" cy="12" rx="4" ry="9.5"/><path d="M2.5 12h19M4 7h16M4 17h16"/></g></svg>
        www.brivotandem.com
      </li>
    </ul>
    <span class="rule rule--two"></span>
    <address class="address">421, Address line goes here<br>45452,Country Name</address>
  </section>

  <section class="card card--back">
    <div class="wordmark">
      <span class="wordmark__square"></span>
      <span class="wordmark__name">Brivo Engineering Tandem</span>
    </div>
    <div class="web">
      <span class="web__line"></span>
      <span>www.<span class="web__accent">brivotandem</span>.com</span>
      <span class="web__line"></span>
    </div>
  </section>
</main>
</body>
</html>
```